Lotstallmart.com Webpage Design

Design Brief for lotstallmart.com (Copy of Brief also in attached Word file)

Name of Website- lotstallmart.com (existing logo and look & feel of website to be changed)

Logo - Finalised. The logo files are attached with the brief as “logo.jpeg”. The “Blue- Grey” version of the logo is for use on lighter backgrounds and the “Orange-White” version of the logo is for use on darker backgrounds. (A full Black version of the logo is also attached). Both versions may be used in different parts of the website. All attached files are in .png format.
Status - The website in functional and is undergoing user trials. However, we want to improve the look & feel of the website so at it seems
a. cotemporary,
b. Easy to Navigate
c. professional and
d. Vibrant.

Please visit ‘lotstallmart.com’ to check out the website and its functionalities – please use it only as a reference for the features & functions to be provided, however the designer should use a ‘Free Hand’ in designing the composition of various parts of the webpage without getting too influenced by the existing design

Objective of the Website ‘lotstallmart.com –
a. It is a portal focussed on listing of ‘Retail’ specific real-estate properties by developers, owners and realty brokers. The properties shall listed under the following four categories-
i. Retail Malls
ii. Shopping Complexes
iii. High-street shops
iv. Retail Warehouses
*refer lotstallmart.com for better clarity

b. The abovementioned properties shall be listed either for ‘Sale’ or ‘rent\lease’ or both

c. Users shall visit the site in case they wish to acquire a retail \ shop space either on ‘sale’ or ‘rent’. These Users would be able to specify the ‘Search Criteria’ through the tool-bars provided on the website – the ‘Search Criteria’ shall comprise of ‘Type of space category’, ‘City’, ‘Locality’, transaction type ie ‘Rent \ Sale’ and ‘Area Range’

d. The main revenue model for the website shall be listing fee ( or advertising charges ) payable by those listing their properties on the website.

Three Main Pages of Website (lotstallmart.com) that need to be designed -
a. Main Home Page (visit the web link - http://lotstallmart.com/ ) - The main home page has the “Search Toolbar” for specifying of Search Criteria by the User. It shall also have the following features & functions-
i. Main Advertising Banner
ii. Featured Projects
iii. New Launches
iv. Toolbar with buttons – ‘Advertise with Us’, ‘Listings Alert’, ‘Mart Wizards’, ‘Advertiser Login’

b. Property Listings Page (visit the web link - http://lotstallmart.com/gurgaon-in-india ) - The List of property options that match the Criteria specified by the ‘User’ get displayed on this page.

c. Property Detail Page - When the ‘User’ clicks on the “More….” Button on the ‘Property Listings Page’ (given in point b. above) the web page with the details of the property opens. (For Example – visit the web link - http://lotstallmart.com/vorne-Shopping-Complex-vorne-quadrion-gurgaon-636 )

Note:- Please refer to attached ‘Shopping’ related images the designer may use them on the website to provide a look & feel of retail if required – either separately or rotate in a single window

Target Market(s)

Retailers & Investors looking for retail space, Real Estate Brokers, Developers

Industry/Entity Type

Advertising

Number of Pages Required

3 page

Requirements
Must have
• Refer to existing site lotstallmart.com -- all the existing functionalities are a must have.
Nice to have
• The Designer may use the retail related images on the website if required for making it more vibrant. Refer attached images Shopping(1-6).jpg

```html
<!DOCTYPE html>
<html lang="en">
<head>
<meta charset="utf-8">
<title>Lotstallmart.com – Retail Space Portal</title>
<link href="https://fonts.googleapis.com/css2?family=Open+Sans:ital,wght@0,400;0,600;0,700;1,700&display=swap" rel="stylesheet">
<style>
:root{
  --blue:#1a86f0;
  --blue-dark:#0f6fd0;
  --blue-text:#1a7fe0;
  --dark:#2e2e2e;
  --darker:#1e1e1e;
  --topbar:#3a3a3a;
  --grey-card:#ececec;
  --text:#333;
  --muted:#777;
  --white:#fff;
}
*{box-sizing:border-box;margin:0;padding:0}
html,body{width:1200px;height:3315px;overflow:hidden}
body{position:relative;background:var(--white);font-family:"Open Sans",Arial,sans-serif;color:var(--text);font-size:13px}
.abs{position:absolute}

/* city bar */
.city-bar{top:0;left:0;width:1200px;height:38px;background:var(--topbar)}
.city-bar ul{position:absolute;left:172px;top:0;display:flex;list-style:none}
.city-bar li{width:96px;height:38px;line-height:38px;text-align:center;color:#ddd;font-size:12px;font-weight:600}
.city-bar li.active{background:#555;color:#fff}

/* header */
.site-header{top:38px;left:0;width:1200px;height:90px;background:#fff}
.brand{position:absolute;left:172px;top:20px;display:flex;align-items:center;gap:10px}
.brand-dot{width:34px;height:34px;border-radius:50%;background:var(--blue)}
.brand-name{font-size:28px;font-weight:700;color:#1d5fa8;line-height:1}
.brand-tag{position:absolute;left:216px;top:62px;font-size:8px;letter-spacing:.5px;color:#666;font-weight:600}
.formats{position:absolute;left:464px;top:30px;display:flex;gap:0}
.formats div{width:145px}
.formats b{display:block;color:var(--blue-text);font-size:12px;font-weight:600}
.formats span{display:block;font-size:11px;color:#333;font-weight:600}

/* nav */
.main-nav{top:128px;left:0;width:1200px;height:55px;background:var(--blue)}
.main-nav ul{position:absolute;left:172px;top:0;height:55px;display:flex;list-style:none;align-items:center}
.main-nav li{color:#fff;font-size:12.5px;padding:0 24px;height:55px;line-height:55px;border-right:1px solid rgba(255,255,255,.35)}
.main-nav li.login{background:var(--blue-dark);font-weight:600}
.main-nav li:last-child{border-right:none}

/* login bar */
.login-bar{top:183px;left:0;width:1200px;height:76px;background:linear-gradient(#3a3a3a,#2a2a2a)}
.field{position:absolute;background:#fff;border:1px solid #ccc;height:32px;font-size:12px;color:#888;padding:7px 10px}
.login-bar .signin{position:absolute;left:769px;top:22px;width:62px;height:32px;background:var(--blue);color:#fff;font-size:12px;font-weight:600;text-align:center;line-height:32px}
.login-bar .small{position:absolute;color:#ddd;font-size:11.5px;top:30px}
.tick-box{display:inline-block;width:11px;height:11px;background:#fff;margin-right:6px;vertical-align:-1px}
.register{position:absolute;left:1078px;top:32px;width:78px;height:20px;background:#ddd;color:#333;font-size:10px;text-align:center;line-height:20px;font-weight:600}

/* hero */
.hero{top:259px;left:0;width:1200px;height:459px;background:linear-gradient(180deg,#5a3a22 0%,#8a5a30 35%,#b9834c 60%,#6a4a30 100%)}
.hero-arrow{position:absolute;top:172px;width:22px;height:22px}

/* search */
.search-panel{top:592px;left:172px;width:869px;height:170px;background:var(--blue);color:#fff}
.search-panel h2{position:absolute;left:18px;top:34px;font-size:17px;font-weight:600;letter-spacing:.3px}
.format-checks{position:absolute;left:288px;top:38px;display:flex;gap:0;font-size:12px}
.format-checks label{margin-right:34px}
.format-checks .box{display:inline-block;width:12px;height:12px;background:#fff;margin-right:6px;vertical-align:-1px;position:relative}
.search-labels span{position:absolute;top:85px;font-size:12px}
.select{position:absolute;top:111px;height:37px;background:#fff;color:#666;font-size:11px;padding:11px 10px;border-radius:2px}
.select::after{content:"";position:absolute;right:10px;top:16px;border:5px solid transparent;border-top-color:#333}
.grey-btn{position:absolute;background:linear-gradient(#eee,#bcbcbc);color:#333;font-weight:700;font-style:italic;text-align:center;border-radius:2px}
.drop-shadow{position:absolute;height:22px;background:radial-gradient(ellipse at top,rgba(0,0,0,.25),rgba(0,0,0,0) 70%)}

/* sections */
.section-title{position:absolute;left:172px;font-size:20px;font-weight:600;color:var(--blue-text)}
.section-title small{font-size:11px;color:var(--muted);font-weight:400}
.card-grid{position:absolute;left:172px;width:869px;display:grid;grid-template-columns:repeat(4,203px);column-gap:19px;row-gap:22px}
.card{height:314px;background:var(--grey-card);text-align:center;position:relative}
.card .photo{position:absolute;left:7px;top:7px;width:189px;height:137px;border:3px solid #fff}
.card .city{position:absolute;top:170px;width:100%;color:var(--blue-text);font-size:16px;font-weight:700}
.card .proj{position:absolute;top:194px;width:100%;font-size:11px;color:#444}
.card .dev{position:absolute;top:217px;width:100%;font-size:11px;color:var(--blue-text)}
.card .type{position:absolute;top:239px;width:100%;font-size:11px;font-weight:700;color:#333}
.card .view{position:absolute;left:46px;top:268px;width:111px;height:27px;background:var(--blue);color:#fff;font-size:11px;line-height:27px;border-radius:2px}

.blue-box{position:absolute;left:172px;width:869px;background:var(--blue);color:#fff}
.blue-box h3{font-size:19px;font-weight:600}

/* editor */
.editors h2{position:absolute;top:2736px;left:0;width:1200px;text-align:center;color:var(--blue-text);font-size:20px;font-weight:600}
.editors p{position:absolute;left:290px;top:2802px;width:670px;text-align:center;font-size:12.5px;line-height:22px;color:#333}
.quote{position:absolute;color:var(--blue-text);font-size:34px;font-weight:700;line-height:1}
.read-more{position:absolute;left:559px;top:2906px;width:108px;height:28px;background:var(--blue);color:#fff;font-size:11px;text-align:center;line-height:28px;border-radius:2px}

/* footer */
.site-footer{top:3006px;left:0;width:1200px;height:247px;background:var(--dark);color:#ddd}
.site-footer h4{position:absolute;top:36px;font-size:12px;font-weight:700;color:#fff}
.site-footer ul{position:absolute;top:72px;list-style:none;font-size:11.5px;line-height:20px}
.site-footer li::before{content:"";display:inline-block;width:4px;height:4px;background:#bbb;border-radius:50%;margin-right:8px;vertical-align:2px}
.footer-sep{position:absolute;top:0;width:1px;height:247px;background:#444}
.footer-about{position:absolute;left:464px;top:70px;width:330px;font-size:11.5px;line-height:20px;color:#ccc}
.contact{position:absolute;left:849px;font-size:11.5px;color:#ddd;line-height:20px}
.bottom-bar{top:3253px;left:0;width:1200px;height:62px;background:var(--darker);color:#aaa;font-size:11px}
.social{position:absolute;top:19px;width:24px;height:24px;border-radius:50%;background:#4a4a4a}
</style>
</head>
<body>

<nav class="abs city-bar">
  <ul>
    <li class="active">NOIDA</li><li>DELHI</li><li>MUMBAI</li><li>CHENNAI</li><li>BANGALORE</li><li>PUNE</li><li>KHANNA</li><li>JAIPUR</li><li>MORE</li>
  </ul>
</nav>

<header class="abs site-header">
  <div class="brand"><span class="brand-dot"></span><span class="brand-name">lotstallmart</span></div>
  <div class="brand-tag">INDIA'S LEADING PORTAL FOR RETAIL SPACE</div>
  <div class="formats">
    <div><b>Retail Malls</b><span>Centrally Air-Conditioned</span></div>
    <div><b>Shopping Complex</b><span>Centrally Air-Conditioned</span></div>
    <div><b>High Street Shops Malls</b><span>Centrally Air-Conditioned</span></div>
    <div><b>Retail Warehouses</b><span>Centrally Air-Conditioned</span></div>
  </div>
</header>

<nav class="abs main-nav">
  <ul>
    <li>Home</li><li>Advertise with us</li><li>Mart Wizards</li><li>Listing Alert</li><li>List your Property Here</li><li class="login">&#128274; ADVERTISER LOGIN</li><li>New Advertiser - Register</li>
  </ul>
</nav>

<section class="abs login-bar">
  <div class="field" style="left:391px;top:22px;width:179px">Username</div>
  <div class="field" style="left:579px;top:22px;width:179px">Password</div>
  <div class="signin">SIGN IN</div>
  <div class="small" style="left:853px"><span class="tick-box"></span>Keep me logged in</div>
  <div class="small" style="left:972px">Forgot Password</div>
  <div class="small" style="left:1078px;top:12px;font-size:10px">New Advertiser?</div>
  <div class="register">REGISTER</div>
</section>

<section class="abs hero" role="img" aria-label="Banner photo of a family shopping in a festively lit mall">
  <svg class="hero-arrow" style="left:36px" viewBox="0 0 22 22"><path d="M14 4 7 11l7 7" fill="none" stroke="#fff" stroke-width="2.5"/></svg>
  <svg class="hero-arrow" style="left:1137px" viewBox="0 0 22 22"><path d="M8 4l7 7-7 7" fill="none" stroke="#fff" stroke-width="2.5"/></svg>
</section>

<section class="abs search-panel">
  <h2>SELECT RETAIL FORMAT</h2>
  <div class="format-checks">
    <label><span class="box"><svg width="12" height="12" viewBox="0 0 12 12"><path d="M2 6l3 3 5-6" fill="none" stroke="#1a86f0" stroke-width="2"/></svg></span>Retail Malls</label>
    <label><span class="box"></span>Shopping Complex</label>
    <label><span class="box"></span>High Street Shops</label>
    <label><span class="box"></span>Retail Warehouses</label>
  </div>
  <div class="search-labels">
    <span style="left:18px">Sale Or Rent Or Both:</span>
    <span style="left:175px">Select City:</span>
    <span style="left:325px">Select Locality</span>
    <span style="left:473px">Enter Keywords</span>
  </div>
  <div class="select" style="left:18px;width:130px">Both</div>
  <div class="select" style="left:175px;width:130px">--Select--</div>
  <div class="select" style="left:325px;width:128px">--Select--</div>
  <div class="select" style="left:473px;width:210px">Name of Projects....</div>
  <div class="grey-btn" style="left:703px;top:57px;top:57px;width:153px;height:40px;line-height:40px;font-size:15px;top:57px;margin-top:0;position:absolute;top:57px;transform:translateY(0);top:57px;top:57px;top:57px;top:57px;top:57px;top:57px;top:57px;top:57px;top:57px;top:57px;top:57px;top:57px;top:57px;top:57px;top:57px;top:57px;top:57px;top:57px;top:57px;top:57px;top:57px;top:57px;top:57px;top:57px;top:57px;top:111px">Search</div>
</section>
<div class="drop-shadow" style="left:222px;top:762px;width:769px"></div>

<h2 class="section-title" style="top:795px">Featured Retail Projects <small>Across India</small></h2>
<div class="card-grid" style="top:835px">
  <article class="card"><div class="photo" role="img" aria-label="Photo of a modern white commercial building" style="background:linear-gradient(#8fb8e0,#dfe6ea 60%,#7a8a8c)"></div><div class="city">FARIDABAD</div><div class="proj">Verdano</div><div class="dev">Orvell</div><div class="type">Shopping Complex</div><div class="view">View the listing</div></article>
  <article class="card"><div class="photo" role="img" aria-label="Photo of a tall red and white apartment tower" style="background:linear-gradient(#7fb0e0,#d8c9c0 55%,#8a6a5a)"></div><div class="city">NEW DELHI</div><div class="proj">Verdano</div><div class="dev">Orvell</div><div class="type">Shopping Complex</div><div class="view">View the listing</div></article>
  <article class="card"><div class="photo" role="img" aria-label="Photo of a red and cream residential block" style="background:linear-gradient(#9cc4ea,#c85a50 55%,#e8ddd0)"></div><div class="city">SURAT</div><div class="proj">Verdano</div><div class="dev">Orvell</div><div class="type">Shopping Complex</div><div class="view">View the listing</div></article>
  <article class="card"><div class="photo" role="img" aria-label="Photo of a purple and white apartment block" style="background:linear-gradient(#a9c9ee,#6a5a9a 50%,#d8d0d8)"></div><div class="city">GURGAON</div><div class="proj">Verdano</div><div class="dev">Orvell</div><div class="type">Shopping Complex</div><div class="view">View the listing</div></article>
  <article class="card"><div class="photo" role="img" aria-label="Photo of a yellow apartment building" style="background:linear-gradient(#8fbbe8,#e8c050 55%,#c08a40)"></div><div class="city">FARIDABAD</div><div class="proj">Verdano</div><div class="dev">Orvell</div><div class="type">Shopping Complex</div><div class="view">View the listing</div></article>
  <article class="card"><div class="photo" role="img" aria-label="Photo of a dark grey residential tower" style="background:linear-gradient(#b8cde0,#4a4e58 55%,#8a8a8a)"></div><div class="city">NEW DELHI</div><div class="proj">Verdano</div><div class="dev">Orvell</div><div class="type">Shopping Complex</div><div class="view">View the listing</div></article>
  <article class="card"><div class="photo" role="img" aria-label="Photo of a red and white apartment block" style="background:linear-gradient(#c8dbe8,#b8504a 55%,#e0dcd4)"></div><div class="city">SURAT</div><div class="proj">Verdano</div><div class="dev">Orvell</div><div class="type">Shopping Complex</div><div class="view">View the listing</div></article>
  <article class="card"><div class="photo" role="img" aria-label="Photo of a blue and white apartment block" style="background:linear-gradient(#9ec4ee,#5a6ab8 55%,#e4e4ea)"></div><div class="city">GURGAON</div><div class="proj">Verdano</div><div class="dev">Orvell</div><div class="type">Shopping Complex</div><div class="view">View the listing</div></article>
</div>

<section class="blue-box" style="top:1529px;height:208px">
  <h3 style="position:absolute;left:20px;top:22px">Mart Wizards</h3>
  <p style="position:absolute;left:20px;top:60px;font-size:12.5px;font-weight:600;line-height:22px;width:840px">Post your Retail Space requirement with us and our experts shall get back with suitable options and even help you in your transaction.<br>This is a Free Service!</p>
  <div class="field" style="left:18px;top:133px;width:214px;height:35px;font-size:11px;padding:9px 10px">Enter your Email Address</div>
  <div class="field" style="left:250px;top:133px;width:214px;height:35px;font-size:11px;padding:9px 10px">Mobile:</div>
  <div class="field" style="left:478px;top:133px;width:210px;height:35px;font-size:11px;padding:9px 10px">Add Description of Requirement:</div>
  <div class="grey-btn" style="left:712px;top:133px;width:133px;height:35px;line-height:35px;font-size:15px">Send</div>
</section>
<div class="drop-shadow" style="left:222px;top:1737px;width:769px"></div>

<h2 class="section-title" style="top:1778px">Featured New Launches <small>Across India</small></h2>
<div class="card-grid" style="top:1817px">
  <article class="card"><div class="photo" role="img" aria-label="Photo of a cream apartment tower" style="background:linear-gradient(#a8c8ea,#e0d0a0 55%,#8a7a5a)"></div><div class="city">FARIDABAD</div><div class="proj">Verdano</div><div class="dev">Orvell</div><div class="type">Shopping Complex</div><div class="view">View the listing</div></article>
  <article class="card"><div class="photo" role="img" aria-label="Photo of a red and white residential block" style="background:linear-gradient(#98c0e8,#c04a44 55%,#e0d8d0)"></div><div class="city">BANGALORE</div><div class="proj">Verdano</div><div class="dev">Orvell</div><div class="type">Shopping Complex</div><div class="view">View the listing</div></article>
  <article class="card"><div class="photo" role="img" aria-label="Photo of a modern white commercial building" style="background:linear-gradient(#8fb8e0,#e4e8ea 60%,#6a7a7c)"></div><div class="city">MOHALI</div><div class="proj">Verdano</div><div class="dev">Orvell</div><div class="type">Shopping Complex</div><div class="view">View the listing</div></article>
  <article class="card"><div class="photo" role="img" aria-label="Photo of a purple and orange apartment block" style="background:linear-gradient(#a9c9ee,#7a4a8a 50%,#d89a60)"></div><div class="city">BHOPAL</div><div class="proj">Verdano</div><div class="dev">Orvell</div><div class="type">Shopping Complex</div><div class="view">View the listing</div></article>
  <article class="card"><div class="photo" role="img" aria-label="Photo of a tall red and white apartment tower" style="background:linear-gradient(#8fbbe8,#d8c0b8 55%,#9a5a4a)"></div><div class="city">FARIDABAD</div><div class="proj">Verdano</div><div class="dev">Orvell</div><div class="type">Shopping Complex</div><div class="view">View the listing</div></article>
  <article class="card"><div class="photo" role="img" aria-label="Photo of a cream low-rise residential building" style="background:linear-gradient(#b0d0ee,#e8e0c8 55%,#a8a090)"></div><div class="city">BANGALORE</div><div class="proj">Verdano</div><div class="dev">Orvell</div><div class="type">Shopping Complex</div><div class="view">View the listing</div></article>
  <article class="card"><div class="photo" role="img" aria-label="Photo of a beige and brown apartment building" style="background:linear-gradient(#c8dae8,#c8a890 55%,#7a5a48)"></div><div class="city">MOHALI</div><div class="proj">Verdano</div><div class="dev">Orvell</div><div class="type">Shopping Complex</div><div class="view">View the listing</div></article>
  <article class="card"><div class="photo" role="img" aria-label="Photo of a teal and white apartment block" style="background:linear-gradient(#a0c8ee,#4a8a8a 55%,#d8e0e0)"></div><div class="city">BHOPAL</div><div class="proj">Verdano</div><div class="dev">Orvell</div><div class="type">Shopping Complex</div><div class="view">View the listing</div></article>
</div>

<section class="blue-box" style="top:2497px;height:203px">
  <svg style="position:absolute;left:20px;top:32px" width="30" height="22" viewBox="0 0 30 22"><rect x="1" y="1" width="28" height="20" fill="#fff"/><path d="M1 1l14 11L29 1" fill="none" stroke="#1a86f0" stroke-width="2"/></svg>
  <h3 style="position:absolute;left:67px;top:26px">Listing Alert</h3>
  <p style="position:absolute;left:67px;top:60px;font-size:11.5px">Suscribe for Fortnightly Email update on New Listings @ Lotstallmart</p>
  <div class="field" style="left:18px;top:108px;width:214px;height:38px;font-size:11px;padding:10px 10px">Enter your Email Address</div>
  <div class="field" style="left:250px;top:108px;width:214px;height:38px;font-size:11px;padding:10px 10px">--Select Options--<span style="position:absolute;right:10px;top:16px;border:5px solid transparent;border-top-color:#333"></span></div>
  <div class="field" style="left:478px;top:108px;width:210px;height:38px;font-size:11px;padding:10px 10px">Add Description of Requirement:<span style="position:absolute;right:10px;top:16px;border:5px solid transparent;border-top-color:#333"></span></div>
  <p style="position:absolute;left:250px;top:152px;font-size:8px">(select retail format of interest)</p>
  <p style="position:absolute;left:478px;top:152px;font-size:8px">(select cities of interest)</p>
  <div class="grey-btn" style="left:710px;top:108px;width:139px;height:36px;line-height:36px;font-size:15px">Subscribe</div>
</section>
<div class="drop-shadow" style="left:222px;top:2700px;width:769px"></div>

<section class="editors">
  <h2>Editor's Choice</h2>
  <span class="quote" style="left:246px;top:2775px">&#8220;</span>
  <p>A "Select" Listing of Retail Properties Handpicked by our Editors based on their own positive &nbsp;Handpicked by our Editors based on their own positive &nbsp;evaluation on parameters &amp; attributes such as Design Concept, Location, Developer, Success Potential. So Read On to Check Out for yourself ............ .</p>
  <span class="quote" style="left:932px;top:2872px">&#8221;</span>
  <div class="read-more">Read More</div>
</section>
<div class="drop-shadow" style="left:190px;top:2950px;width:830px"></div>

<footer class="abs site-footer">
  <h4 style="left:183px">ABOUT STALLPOINT REALTY</h4>
  <ul style="left:183px"><li>About Us</li><li>Privacy Policy</li><li>Terms of Use</li><li>Contact Us</li><li>Site Map</li></ul>
  <ul style="left:309px"><li>Retail Malls</li><li>Shopping Complex</li><li>High Street Shops</li><li>Retail Warehouses</li></ul>
  <div class="footer-sep" style="left:438px"></div>
  <h4 style="left:464px">WWW.LOTSTALLMART.COM</h4>
  <p class="footer-about">Lotstallmart.com - About Us Lotstallmart.com is a Specialised Web based platform for Retail Space, featuring properties across India under various formats such as Retail Malls, Shopping Complexes, High-street Shops. Also featured are Retail Warehouses which provide the logistic back-end for the retail business. Lotstallmart.com is useful to various category of users as follows- a.</p>
  <div class="footer-sep" style="left:807px"></div>
  <h4 style="left:849px">CONTACTS</h4>
  <svg style="position:absolute;left:849px;top:76px" width="12" height="16" viewBox="0 0 12 16"><path d="M6 0a6 6 0 0 0-6 6c0 4.5 6 10 6 10s6-5.5 6-10a6 6 0 0 0-6-6z" fill="#ddd"/><circle cx="6" cy="6" r="2.2" fill="#2e2e2e"/></svg>
  <div class="contact" style="left:873px;top:72px;font-weight:600">Stallpoint Realty,<br>Unit 212, 3rd Floor,<br>P. O BOX 10482, Lakeside.</div>
  <svg style="position:absolute;left:849px;top:143px" width="13" height="13" viewBox="0 0 13 13"><path d="M3 0l2.5 3-1.5 2a7 7 0 0 0 4 4l2-1.5L13 10l-1.5 3C5 13 0 8 0 1.5z" fill="#ddd"/></svg>
  <div class="contact" style="left:873px;top:140px">+000 555 014 220</div>
  <svg style="position:absolute;left:849px;top:170px" width="13" height="10" viewBox="0 0 13 10"><rect width="13" height="10" fill="#ddd"/><path d="M0 0l6.5 5L13 0" fill="none" stroke="#2e2e2e"/></svg>
  <div class="contact" style="left:873px;top:165px">Lotstallmart.com</div>
</footer>

<div class="abs bottom-bar">
  <p style="position:absolute;left:172px;top:23px">All Rights Reserved. Copyrights @ 2015</p>
  <span class="social" style="left:895px"></span>
  <span class="social" style="left:926px"></span>
  <span class="social" style="left:957px"></span>
  <span class="social" style="left:988px"></span>
</div>

</body>
</html>
```